Redesign of business card for Cedar Ridge Mechanical

We are looking for a new design for our business cards for Cedar Ridge Mechanical. We are a plumbing & HVAC construction company, operating on the West Coast of Canada and USA. Logo attached.
Industry/Entity Type
Construction - Plumbing & HVAC
Contact Information for Business Card
Name, address, phone numbers, email, website address
Look and feel
Each slider illustrates characteristics of the customer's brand and the style your logo design should communicate.

```html
<!DOCTYPE html>
<html lang="en">
<head>
<meta charset="utf-8">
<title>Cedar Ridge Mechanical – Business Card</title>
<link rel="stylesheet" href="https://fonts.googleapis.com/css2?family=Montserrat:wght@400;700&display=swap">
<style>
  :root {
    --backdrop: #cfd4d4;
    --card: #f0f0ef;
    --ink: #111111;
    --ink-soft: #555555;
    --rule: #222222;
  }
  * { box-sizing: border-box; margin: 0; padding: 0; }
  html, body {
    width: 1200px; height: 881px; overflow: hidden;
    background: var(--backdrop);
    font-family: "Montserrat", sans-serif;
    color: var(--ink);
  }
  .stage {
    position: relative; width: 1200px; height: 881px;
  }
  .card {
    position: absolute; top: 285px;
    width: 540px; height: 310px;
    background: var(--card);
    border-radius: 3px;
  }
  .card--front { left: 40px; }
  .card--back { left: 620px; }

  /* front */
  .brand {
    position: absolute; left: 30px; top: 0; bottom: 0; width: 210px;
    display: flex; align-items: center; gap: 12px;
  }
  .brand__mark {
    flex: none; width: 22px; height: 22px; background: var(--ink);
  }
  .brand__name {
    font-weight: 700; font-size: 19px; line-height: 1.2;
    letter-spacing: 0.5px; text-transform: uppercase;
  }
  .divider {
    position: absolute; left: 262px; top: 70px; width: 1.5px; height: 170px;
    background: var(--rule);
  }
  .contact {
    position: absolute; left: 286px; top: 72px; right: 20px;
  }
  .contact__name {
    font-weight: 700; font-size: 19px; letter-spacing: 0.6px; text-transform: uppercase;
  }
  .contact__role {
    font-size: 12.5px; color: var(--ink-soft); margin-top: 2px;
  }
  .contact__address {
    font-size: 12.5px; color: var(--ink-soft); margin-top: 12px; line-height: 1.4;
  }
  .contact__list { list-style: none; margin-top: 10px; }
  .contact__item {
    display: flex; align-items: center; gap: 8px;
    font-size: 12.5px; color: var(--ink); line-height: 1.65;
  }
  .contact__icon { width: 10px; height: 10px; flex: none; fill: var(--ink); }

  /* back */
  .card--back .brand-large {
    position: absolute; inset: 0;
    display: flex; align-items: center; justify-content: center; gap: 18px;
  }
  .brand-large__mark { width: 36px; height: 36px; background: var(--ink); flex: none; }
  .brand-large__name {
    font-weight: 700; font-size: 30px; line-height: 1.15;
    letter-spacing: 0.8px; text-transform: uppercase;
  }
</style>
</head>
<body>
<main class="stage">
  <section class="card card--front" aria-label="Business card front">
    <div class="brand">
      <span class="brand__mark"></span>
      <span class="brand__name">Cedar Ridge<br>Mechanical</span>
    </div>
    <div class="divider"></div>
    <div class="contact">
      <p class="contact__name">Daniel Reyes</p>
      <p class="contact__role">Managing Director</p>
      <p class="contact__address">Your address, City<br>State, Zip 1234</p>
      <ul class="contact__list">
        <li class="contact__item">
          <svg class="contact__icon" viewBox="0 0 10 10"><path d="M2 0.5 L3.6 2.6 L2.7 3.6 Q3.8 5.9 6.3 7.2 L7.4 6.3 L9.5 7.9 L8.4 9.5 Q1 8 0.5 1.6 Z"/></svg>
          123 456 789
        </li>
        <li class="contact__item">
          <svg class="contact__icon" viewBox="0 0 10 10"><path d="M0.5 2 H9.5 V8.5 H0.5 Z M1.3 2.6 L5 5.5 L8.7 2.6" fill="none" stroke="#111" stroke-width="1"/></svg>
          info@youremail.com
        </li>
        <li class="contact__item">
          <svg class="contact__icon" viewBox="0 0 10 10"><circle cx="5" cy="5" r="4.3" fill="none" stroke="#111" stroke-width="1"/><path d="M0.7 5 H9.3 M5 0.7 Q2.5 5 5 9.3 M5 0.7 Q7.5 5 5 9.3" fill="none" stroke="#111" stroke-width="0.8"/></svg>
          www.yourwebsite.com
        </li>
      </ul>
    </div>
  </section>

  <section class="card card--back" aria-label="Business card back">
    <div class="brand-large">
      <span class="brand-large__mark"></span>
      <span class="brand-large__name">Cedar Ridge<br>Mechanical</span>
    </div>
  </section>
</main>
</body>
</html>
```